Lo Mara Menu Design Project

This project is pretty straight forward. You will be given 3 files which include the following:
1. Our proposed menu
2. Our Company logo
3. A sample menu on what we are looking for design wise

Your job is to create a visually pleasing menu that is simple, clean and fresh. Please refer to our home website for additional information. (www.lomara-eats.com) Must be in eps or equivalent format.

Target Market(s)

20s to 40s

Industry/Entity Type

It Company

Requirements
Must have
• Company log
Must be in EPS format

```html
<!DOCTYPE html>
<html lang="en">
<head>
<meta charset="utf-8">
<title>Lo Mara Menu</title>
<link rel="stylesheet" href="https://fonts.googleapis.com/css2?family=Arimo:wght@400;700&family=Source+Sans+3:wght@400&family=Tinos:wght@700&display=swap">
<style>
  :root {
    --backdrop: #d9d6d2;
    --menu-bg: #303032;
    --menu-bg-edge: #262628;
    --ink: #ffffff;
    --ink-soft: #e6e6e6;
    --photo-pasta: #b2532c;
    --photo-pasta-light: #e0a15f;
    --photo-noodle: #c9a86a;
    --photo-noodle-light: #ecd7a6;
    --photo-beef: #3b2418;
    --photo-beef-light: #4f6a2a;
  }
  * { margin: 0; padding: 0; box-sizing: border-box; }
  html, body { width: 1097px; height: 1200px; overflow: hidden; }
  body { background: var(--backdrop); position: relative; }

  .menu {
    position: absolute;
    left: 115px; top: 41px;
    width: 867px; height: 1117px;
    background: radial-gradient(ellipse at 50% 40%, var(--menu-bg) 0%, var(--menu-bg-edge) 100%);
    color: var(--ink);
    overflow: hidden;
  }

  .photo-band { position: absolute; left: 0; top: 0; width: 867px; height: 165px; }
  .photo { position: absolute; top: 0; height: 165px; }
  .photo--pasta { left: 0; width: 320px; background: radial-gradient(ellipse at 40% 45%, var(--photo-pasta-light), var(--photo-pasta) 55%, #f2f2f2 80%); }
  .photo--noodles { left: 320px; width: 368px; background: radial-gradient(ellipse at 50% 50%, var(--photo-noodle-light), var(--photo-noodle) 70%, #6b5a3e 100%); }
  .photo--beef { left: 688px; width: 179px; background: radial-gradient(ellipse at 55% 50%, var(--photo-beef-light), var(--photo-beef) 55%, #f4f4f4 85%); }

  .section-title {
    position: absolute; left: 0; width: 867px;
    font-family: "Arimo", sans-serif; font-weight: 400;
    font-size: 38px; text-align: center; letter-spacing: 1px;
  }
  .section-title--dimsum { top: 212px; }
  .section-title--starters { top: 752px; }

  .item {
    position: absolute; width: 270px;
    transform: translateX(-50%);
    text-align: center;
  }
  .item--wide { width: 320px; }
  .item__name, .item__price {
    font-family: "Tinos", serif; font-weight: 700;
    font-size: 17px; line-height: 22px;
  }
  .item__desc {
    margin-top: 6px;
    font-family: "Source Sans 3", sans-serif;
    font-size: 13.5px; line-height: 18px;
    color: var(--ink-soft);
  }

  .col-left { left: 170px; }
  .col-mid { left: 431px; }
  .col-right { left: 685px; }

  .combo {
    position: absolute; left: 0; top: 972px; width: 867px;
    text-align: center;
  }
  .combo__desc {
    margin: 8px auto 0; width: 640px;
    font-family: "Source Sans 3", sans-serif;
    font-size: 13.5px; line-height: 18px; color: var(--ink-soft);
  }
</style>
</head>
<body>
  <main class="menu">
    <div class="photo-band">
      <div class="photo photo--pasta" role="img" aria-label="Plate of pasta in red sauce"></div>
      <div class="photo photo--noodles" role="img" aria-label="Stir-fried noodles with shrimp"></div>
      <div class="photo photo--beef" role="img" aria-label="Beef with green beans"></div>
    </div>

    <h2 class="section-title section-title--dimsum">DIM SUM</h2>

    <section class="item col-left" style="top:283px">
      <div class="item__name">Pan-Fried Potstickers</div>
      <div class="item__price">$ 6.50</div>
      <p class="item__desc">Five pan-Fried potstickers with<br>chicken or pork.<br>Served with apricot dipping sauce</p>
    </section>
    <section class="item col-left" style="top:415px">
      <div class="item__name">Spring Rolls</div>
      <div class="item__price">$ 4.50</div>
      <p class="item__desc">Two chicken or vegetable<br>spring rolls. Served with apricot<br>dipping sauce</p>
    </section>
    <section class="item col-left" style="top:556px">
      <div class="item__name">Shrimp Toast</div>
      <div class="item__price">$ 5.95</div>
      <p class="item__desc">Four pieces of fried toast with<br>shrimp, onions, bamboo shoots, and<br>water chestnuts. Served with apricot<br>dipping sauce.</p>
    </section>

    <section class="item col-mid" style="top:329px">
      <div class="item__name">Szechuan Dumplings</div>
      <div class="item__price">$ 6.25</div>
      <p class="item__desc">Five chicken dumplings<br>tossed in a spicy cilantro<br>sauce.</p>
    </section>
    <section class="item item--wide col-mid" style="top:462px">
      <div class="item__name">Wonton Stars</div>
      <div class="item__price">$ 7.25</div>
      <p class="item__desc" style="margin-top:0">Five crispy wonton skins filled<br>with real crab and seasoned cream cheese.<br>Served with sweet and sour dipping sauce.</p>
    </section>
    <section class="item col-mid" style="top:599px">
      <div class="item__name">Shu Mai</div>
      <div class="item__price">$ 5.95</div>
      <p class="item__desc">Six steamed open-Face dumplings<br>with pork<br>shrimp, and mushrooms.</p>
    </section>

    <section class="item col-right" style="top:283px">
      <div class="item__name">Steamed Dumplings</div>
      <div class="item__price">$ 6.50</div>
      <p class="item__desc">Five steamed dumplings with<br>chicken, or  vegetables.<br>Served with apricot dipping sauce.</p>
    </section>
    <section class="item col-right" style="top:415px">
      <div class="item__name">Bao</div>
      <div class="item__price">$ 5.95</div>
      <p class="item__desc">Three fluffy steamed chinese<br>buns filled with barbeque<br>pork.</p>
    </section>
    <section class="item col-right" style="top:556px">
      <div class="item__name">Gift Wrapped Chicken</div>
      <div class="item__price">$5.95</div>
      <p class="item__desc">Six chicken breast tenders marinated<br>in soy sauce<br>sesame oil, and cilantro.</p>
    </section>

    <h2 class="section-title section-title--starters">STARTERS</h2>

    <section class="item col-left" style="top:827px">
      <div class="item__name">Lightly Battered Calamari Strips</div>
      <div class="item__price">$ 5.95</div>
      <p class="item__desc">Six calamari strips, lightly battered<br>with a garlic ginger aioli.</p>
    </section>
    <section class="item col-mid" style="top:852px">
      <div class="item__name">Edamame</div>
      <div class="item__price">$ 4.00</div>
      <p class="item__desc">Steamed Soybean Pods.</p>
    </section>
    <section class="item col-right" style="top:827px">
      <div class="item__name">4 C's Lo Mara Crab Cake's</div>
      <div class="item__price">$11.95</div>
      <p class="item__desc">Jumbo lump Maryland crab meat<br>with seasoned<br>with our Lo Mara spice blend.<br>Topped with a kick  of spicy aioli.</p>
    </section>

    <section class="combo">
      <div class="item__name">Dim Sum And Then Sum &nbsp;&nbsp;(Lunch / Dinner)</div>
      <div class="item__price">$ 14.95 / 18.95</div>
      <p class="combo__desc">Choose three / four half orders: Potstickers, steamed dumplings, szechwan dumplings,<br>spring roll, shrimp toast, chinese chicken salad, hot &amp; sour soup, wonton soup, or mushu.<br>For Shrimp fried rice, beef fried rice, or mushu shrimp, add $1.00.</p>
    </section>
  </main>
</body>
</html>
```